Coastline Premier Retreats Business Card Design

Design a business card for Coastline Premier Retreats. Look at the website for colors and reference. Card should have logo, name, title, office number, mobile number, email, URL and a tagline like, "Luxury Hotel & Resort Email Marketing" (This might change).

https://www.coastlinepremierretreats.example

The rest I will leave up to your imagination.

Contact Information for Business Card

Logo, name, title, office number, mobile number, email, URL and a tagline like, "Luxury Hotel & Resort Email Marketing" (This might change).

```html
<!DOCTYPE html>
<html lang="en">
<head>
<meta charset="utf-8">
<title>Coastline Premier Retreats – Business Card</title>
<link href="https://fonts.googleapis.com/css2?family=Open+Sans:wght@400;600;700;800&display=swap" rel="stylesheet">
<style>
  :root {
    --charcoal: #222226;
    --orange: #f37321;
    --orange-deep: #e0621a;
    --white: #ffffff;
    --backdrop: #d9dadc;
  }
  * { box-sizing: border-box; margin: 0; padding: 0; }
  html, body { width: 1200px; height: 780px; overflow: hidden; }
  body {
    background: var(--backdrop);
    font-family: "Open Sans", Arial, sans-serif;
    position: relative;
  }
  .card {
    position: absolute;
    top: 235px;
    width: 540px;
    height: 310px;
    box-shadow: 0 10px 28px rgba(0,0,0,.22);
    overflow: hidden;
  }

  /* Front */
  .card-front { left: 45px; background: var(--charcoal); }
  .tagline-band {
    position: absolute; left: 0; top: 0; bottom: 0; width: 96px;
    background: var(--orange);
    display: flex; align-items: center; justify-content: center;
  }
  .tagline {
    transform: rotate(90deg);
    white-space: nowrap;
    color: var(--white);
    font-size: 15px; line-height: 1.3; text-align: center;
    font-weight: 400;
  }
  .brand-name {
    position: absolute; left: 190px; top: 34px;
    color: var(--white);
    font-weight: 800; font-size: 25px; letter-spacing: .5px;
    text-transform: uppercase; line-height: 1.05;
  }
  .brand-mark {
    display: inline-block; width: 14px; height: 14px;
    background: var(--orange); margin-right: 10px; vertical-align: 2px;
  }
  .name-tab {
    position: absolute; right: 0; top: 116px; width: 14px; height: 40px;
    background: var(--orange);
  }
  .person {
    position: absolute; right: 36px; top: 112px; text-align: right;
  }
  .person-name { font-size: 27px; font-weight: 700; color: var(--white); line-height: 1.1; }
  .person-name .first { color: var(--orange); }
  .person-title { font-size: 14px; color: var(--white); margin-top: 2px; }
  .contact {
    position: absolute; right: 22px; top: 196px;
    list-style: none; text-align: right;
  }
  .contact li {
    color: var(--white); font-size: 12.5px; line-height: 19px;
    display: flex; justify-content: flex-end; align-items: center; gap: 10px;
  }
  .contact svg { width: 12px; height: 12px; fill: none; stroke: var(--orange); stroke-width: 1.6; }

  /* Back */
  .card-back {
    left: 615px; background: var(--orange);
    display: flex; align-items: center; justify-content: center;
  }
  .emboss-name {
    color: var(--orange-deep);
    font-weight: 800; font-size: 34px; text-transform: uppercase;
    letter-spacing: 1px; text-align: center; line-height: 1.1;
  }
</style>
</head>
<body>
  <section class="card card-front" aria-label="Business card front">
    <div class="tagline-band">
      <p class="tagline">Luxury Hotel &amp;<br>Resort Email Marketing</p>
    </div>

    <div class="brand-name"><span class="brand-mark"></span>Coastline<br>Premier Retreats</div>

    <div class="name-tab"></div>
    <div class="person">
      <p class="person-name"><span class="first">Marta</span> Kovarik</p>
      <p class="person-title">Co-Founder</p>
    </div>

    <ul class="contact">
      <li>(555) 010-2758
        <svg viewBox="0 0 12 12"><path d="M3 1.5 L4.5 4 L3.5 5 Q5 7.5 7 8.5 L8 7.5 L10.5 9 L9.5 10.5 Q4 10 1.5 3 Z"/></svg></li>
      <li>(555) 010-7777
        <svg viewBox="0 0 12 12"><rect x="3" y="1" width="6" height="10" rx="1"/><line x1="5.5" y1="9.3" x2="6.5" y2="9.3"/></svg></li>
      <li>www.coastlinepremierretreats.example
        <svg viewBox="0 0 12 12"><circle cx="6" cy="6" r="4.8"/><ellipse cx="6" cy="6" rx="2" ry="4.8"/><line x1="1.2" y1="6" x2="10.8" y2="6"/></svg></li>
      <li>info@coastlinepremierretreats.example
        <svg viewBox="0 0 12 12"><rect x="1" y="2.5" width="10" height="7"/><path d="M1 2.5 L6 6.5 L11 2.5"/></svg></li>
    </ul>
  </section>

  <section class="card card-back" aria-label="Business card back">
    <p class="emboss-name">Coastline<br>Premier Retreats</p>
  </section>
</body>
</html>
```